The Linen Loft Co

We need a business card design for our wardrobe company.
Please visit our website www.gentlelinenlofts.com to get an idea of who we are.

```html
<!DOCTYPE html>
<html lang="en">
<head>
<meta charset="utf-8">
<title>The Linen Loft Co — Business Card</title>
<link href="https://fonts.googleapis.com/css2?family=Montserrat:wght@400;500;700&display=swap" rel="stylesheet">
<style>
  :root {
    --page-bg: #d9dadc;
    --card-dark: #2b2a29;
    --card-light: #ffffff;
    --ink: #222222;
    --gold: #8a7150;
    --on-dark: #ffffff;
    --photo-warm-a: #c9a57e;
    --photo-warm-b: #5a4330;
    --photo-grey-a: #8c8d90;
    --photo-grey-b: #2e2e30;
  }
  * { box-sizing: border-box; margin: 0; padding: 0; }
  html, body { width: 1200px; height: 800px; overflow: hidden; }
  body {
    background: var(--page-bg);
    font-family: "Montserrat", sans-serif;
    color: var(--ink);
    display: flex;
    align-items: center;
    justify-content: center;
    gap: 40px;
  }
  .card {
    width: 540px;
    height: 309px;
    position: relative;
    box-shadow: 0 6px 18px rgba(0,0,0,0.18);
    overflow: hidden;
  }

  /* Back side */
  .card-back { background: var(--card-dark); color: var(--on-dark); }
  .back-brand {
    position: absolute;
    top: 26px; left: 170px;
    display: flex; align-items: center; gap: 16px;
  }
  .brand-square {
    width: 58px; height: 42px;
    border: 2px solid var(--on-dark);
  }
  .back-brand .brand-name {
    font-size: 17px; font-weight: 500; letter-spacing: 2px; text-transform: uppercase;
  }
  .back-brand .brand-tagline {
    font-size: 15px; font-weight: 500; letter-spacing: 1px; margin-top: 4px;
  }
  .photo-strip {
    position: absolute;
    left: 0; right: 0; top: 112px; height: 162px;
    display: grid; grid-template-columns: 1fr 1fr 1fr; gap: 6px;
  }
  .photo { height: 100%; }
  .photo-warm { background: linear-gradient(160deg, var(--photo-warm-a), var(--photo-warm-b)); }
  .photo-grey { background: linear-gradient(170deg, var(--photo-grey-a), var(--photo-grey-b)); }
  .photo-light { background: linear-gradient(160deg, #e2d6c6, #8b7358); }

  /* Front side */
  .card-front { background: var(--card-light); }
  .front-brand {
    position: absolute; left: 34px; top: 86px; width: 210px;
    text-align: center;
  }
  .front-brand .brand-square {
    border-color: var(--gold);
    width: 64px; height: 46px;
    margin: 0 auto 14px;
  }
  .front-brand .brand-name {
    font-size: 17px; font-weight: 500; letter-spacing: 2px; text-transform: uppercase; color: var(--ink);
  }
  .front-brand .brand-tagline {
    font-size: 13px; font-weight: 500; letter-spacing: 0.5px; margin-top: 4px;
  }
  .divider {
    position: absolute; left: 270px; top: 78px;
    width: 1.5px; height: 116px; background: var(--gold);
  }
  .contact { position: absolute; left: 290px; top: 76px; }
  .contact-name { color: var(--gold); font-size: 17px; font-weight: 700; }
  .contact-role { font-size: 12.5px; font-weight: 500; margin: 2px 0 12px; }
  .contact-line {
    display: flex; align-items: center; gap: 8px;
    font-size: 12.5px; font-weight: 500; line-height: 19px;
  }
  .contact-line svg { width: 13px; height: 13px; flex: none; }
  .address {
    position: absolute; left: 0; right: 0; bottom: 42px;
    text-align: center; font-size: 13px; font-weight: 500;
  }
</style>
</head>
<body>

  <section class="card card-back" aria-label="Card back">
    <div class="back-brand">
      <div class="brand-square"></div>
      <div>
        <div class="brand-name">The Linen Loft Co</div>
        <div class="brand-tagline">Everything in its Place</div>
      </div>
    </div>
    <div class="photo-strip">
      <div class="photo photo-warm" role="img" aria-label="Photo of a walk-in wardrobe with warm wooden shelving"></div>
      <div class="photo photo-grey" role="img" aria-label="Photo of a dark dressing room with a round ottoman"></div>
      <div class="photo photo-light" role="img" aria-label="Photo of a lit wardrobe with glass-fronted cabinets"></div>
    </div>
  </section>

  <section class="card card-front" aria-label="Card front">
    <div class="front-brand">
      <div class="brand-square"></div>
      <div class="brand-name">The Linen Loft Co</div>
      <div class="brand-tagline">Everything in its Place</div>
    </div>
    <div class="divider"></div>
    <div class="contact">
      <div class="contact-name">Mara Ellison</div>
      <div class="contact-role">Design Consultant &amp; Dream Maker</div>
      <div class="contact-line">
        <svg viewBox="0 0 16 16" aria-hidden="true"><path fill="#8a7150" d="M3.5 1.5l2.3 0 1 3.2-1.6 1.2a8 8 0 0 0 4.9 4.9l1.2-1.6 3.2 1v2.3c0 .8-.7 1.5-1.5 1.5A12 12 0 0 1 2 3c0-.8.7-1.5 1.5-1.5z"/></svg>
        0207 555 0148
      </div>
      <div class="contact-line">
        <svg viewBox="0 0 16 16" aria-hidden="true"><rect x="1.5" y="3.5" width="13" height="9" fill="none" stroke="#8a7150" stroke-width="1.4"/><path d="M1.5 3.5l6.5 5 6.5-5" fill="none" stroke="#8a7150" stroke-width="1.4"/></svg>
        mara@gentlelinenlofts.com
      </div>
      <div class="contact-line">
        <svg viewBox="0 0 16 16" aria-hidden="true"><g fill="none" stroke="#8a7150" stroke-width="1.2"><circle cx="8" cy="8" r="6.3"/><ellipse cx="8" cy="8" rx="2.8" ry="6.3"/><path d="M1.7 8h12.6"/></g></svg>
        www.gentlelinenlofts.com
      </div>
    </div>
    <div class="address">Harbour Court, 42 Mill Lane, London EC2A 4QT</div>
  </section>

</body>
</html>
```